Looking for a modern, Professional business card design

We have a simple business card, but are looking for a more modern, professional look. A sample of the basic card is attached as well as the logo. We would also like to add that we offer:
Struggling with your finances?
- Learn to become debt free
- Discover the power of cash
- Control your money instead of it controlling you
Let us help you achieve a new level of financial freedom!
Also, we would like to have a "SPECIAL OFFER!: FREE 30 minute consultation"
Financial Planning

```html
<!DOCTYPE html>
<html lang="en">
<head>
<meta charset="utf-8">
<title>Steadyledger Money Coaching – Business Card</title>
<link rel="stylesheet" href="https://fonts.googleapis.com/css2?family=Roboto:wght@400;500;700;900&family=Roboto+Condensed:wght@700&display=swap">
<style>
  :root {
    --backdrop: #2a2a2a;
    --card-white: #ffffff;
    --brand-green: #2ea24a;
    --text-green: #2a9a3e;
    --lime: #8cc63f;
    --deep-green: #1f7a33;
    --ink: #111111;
    --muted: #444444;
  }
  * { margin: 0; padding: 0; box-sizing: border-box; }
  html, body {
    width: 1200px; height: 987px; overflow: hidden;
    background: var(--backdrop);
    font-family: "Roboto", Arial, sans-serif;
  }
  .card {
    position: absolute; left: 293px;
    width: 615px; height: 352px; overflow: hidden;
  }
  /* Front */
  .card--front { top: 123px; background: var(--card-white); }
  .edge-strip {
    position: absolute; right: 0; top: 0; width: 12px; height: 100%;
    background: linear-gradient(to bottom, var(--ink) 0 32%, var(--brand-green) 32% 66%, var(--card-white) 66% 67%, var(--lime) 67% 100%);
  }
  .contact {
    position: absolute; right: 51px; top: 36px; text-align: right;
  }
  .contact__name {
    color: var(--text-green); font-size: 22px; font-weight: 500; letter-spacing: 0.3px;
  }
  .contact__title {
    color: var(--ink); font-size: 17px; margin-top: 4px;
  }
  .contact__list { list-style: none; margin-top: 14px; }
  .contact__item {
    display: flex; justify-content: flex-end; align-items: center; gap: 10px;
    color: var(--muted); font-size: 15px; height: 24px;
  }
  .contact__icon { width: 14px; height: 14px; flex: none; }
  .brand {
    position: absolute; right: 51px; top: 188px;
    display: flex; align-items: center; gap: 18px;
  }
  .brand__dot {
    width: 44px; height: 44px; border-radius: 50%;
    background: var(--lime);
  }
  .brand__name {
    color: var(--ink); font-weight: 900; font-size: 34px; line-height: 1.05;
    text-transform: uppercase; text-align: right; letter-spacing: 0.5px;
  }
  .brand__tagline {
    position: absolute; right: 51px; top: 290px;
    color: var(--muted); font-size: 14px; letter-spacing: 0.3px;
  }
  /* Back */
  .card--back { top: 499px; background: var(--brand-green); color: var(--card-white); }
  .pitch { position: absolute; left: 40px; top: 62px; }
  .pitch__heading { font-size: 18px; font-weight: 500; letter-spacing: 0.2px; }
  .pitch__list { list-style: none; margin-top: 8px; }
  .pitch__list li {
    font-size: 16px; height: 26px; display: flex; align-items: center;
  }
  .pitch__list li::before {
    content: ""; width: 6px; height: 6px; border-radius: 50%;
    background: var(--card-white); margin: 0 10px 0 2px;
  }
  .pitch__promise {
    font-family: "Roboto Condensed", Arial, sans-serif;
    font-weight: 700; font-size: 16px; margin-top: 12px;
  }
  .offer { position: absolute; left: 40px; top: 214px; }
  .offer__title { font-size: 42px; font-weight: 900; letter-spacing: 0.5px; line-height: 1; }
  .offer__detail { font-size: 20px; font-weight: 900; margin-top: 8px; letter-spacing: 0.3px; }
  .brand-decoration {
    position: absolute; right: 0; top: 0; width: 205px; height: 100%;
    background: radial-gradient(ellipse at 60% 45%, var(--lime) 0%, #5fb83f 40%, var(--brand-green) 78%);
  }
</style>
</head>
<body>
  <section class="card card--front">
    <div class="edge-strip"></div>
    <div class="contact">
      <p class="contact__name">DANIEL R. WHITFORD</p>
      <p class="contact__title">Personal Financial Coach</p>
      <ul class="contact__list">
        <li class="contact__item">(555) 014-2738
          <svg class="contact__icon" viewBox="0 0 14 14"><rect x="3" y="0.5" width="8" height="13" rx="1.5" fill="none" stroke="#2a9a3e" stroke-width="1.6"/><rect x="6" y="11" width="2" height="1" fill="#2a9a3e"/></svg>
        </li>
        <li class="contact__item">daniel@steadyledgerplan.com
          <svg class="contact__icon" viewBox="0 0 14 14"><rect x="0.5" y="2.5" width="13" height="9" fill="#2a9a3e"/><path d="M0.5 2.5 L7 8 L13.5 2.5" fill="none" stroke="#fff" stroke-width="1.2"/></svg>
        </li>
        <li class="contact__item">www.steadyledgerplan.com
          <svg class="contact__icon" viewBox="0 0 14 14"><circle cx="7" cy="7" r="6.5" fill="#2a9a3e"/><path d="M1 7 H13 M7 0.5 C4 4 4 10 7 13.5 M7 0.5 C10 4 10 10 7 13.5" fill="none" stroke="#fff" stroke-width="0.9"/></svg>
        </li>
      </ul>
    </div>
    <div class="brand">
      <span class="brand__dot"></span>
      <p class="brand__name">Steadyledger<br>Money Coaching</p>
    </div>
    <p class="brand__tagline">Achieve a new level of personal freedom</p>
  </section>

  <section class="card card--back">
    <div class="pitch">
      <p class="pitch__heading">STRUGGLING WITH YOUR FINANCES?</p>
      <ul class="pitch__list">
        <li>Learn to become debt free</li>
        <li>Discover the power of cash</li>
        <li>Control your money instead of it controlling you</li>
      </ul>
      <p class="pitch__promise">Let us help you achieve a new level of financial freedom!</p>
    </div>
    <div class="offer">
      <p class="offer__title">SPECIAL OFFER!</p>
      <p class="offer__detail">FREE 30 MINUTE CONSULTATION</p>
    </div>
    <div class="brand-decoration" role="img" aria-label="Large decorative brand symbol in green tones"></div>
  </section>
</body>
</html>
```